New Business Card Design Project

Use the flyer uploaded and website www.brightoakbuilders.com for inspiration.
List Our Services on Backside of business cards
Marcus Delling
Harborline Builders Inc.
Licensed General Contractors
858-471-6093

Contact Information for Business Card

Use the flyer uploaded and website www.brightoakbuilders.com for inspiration. List Our Services on Backside of business cards Marcus Delling Harborline Builders Inc. Licensed General Contractors 858-471-6093

```html
<!DOCTYPE html>
<html lang="en">
<head>
<meta charset="utf-8">
<title>Harborline Builders – Business Cards</title>
<link href="https://fonts.googleapis.com/css2?family=Marcellus&family=PT+Sans:wght@400;700&display=swap" rel="stylesheet">
<style>
  :root {
    --backdrop: #3b3b3c;
    --card: #1f1f20;
    --ink: #f2f2f2;
    --ink-soft: #d9d9d9;
    --band-text: #1f1f20;
  }
  * { margin: 0; padding: 0; box-sizing: border-box; }
  html, body { width: 900px; height: 1200px; overflow: hidden; }
  body {
    background: var(--backdrop);
    position: relative;
    font-family: "PT Sans", Arial, sans-serif;
    color: var(--ink);
  }
  .card {
    position: absolute;
    left: 133px;
    width: 633px;
    height: 364px;
    background: var(--card);
  }
  .card--services { top: 210px; }
  .card--contact { top: 624px; }

  .brand-name {
    font-family: "PT Sans", Arial, sans-serif;
    font-weight: 400;
    font-size: 24px;
    letter-spacing: 0.5px;
    white-space: nowrap;
    line-height: 1;
    color: var(--ink);
  }
  .brand--centered {
    position: absolute;
    left: 0; width: 376px;
    top: 226px;
    text-align: center;
  }
  .brand--left {
    position: absolute;
    left: 29px;
    top: 55px;
  }

  .services {
    position: absolute;
    left: 372px;
    top: 54px;
  }
  .services-heading {
    font-weight: 700;
    font-size: 14px;
    line-height: 18px;
    text-transform: uppercase;
  }
  .services-band {
    display: inline-block;
    margin-top: 2px;
    background: var(--ink);
    color: var(--band-text);
    font-weight: 700;
    font-size: 14px;
    letter-spacing: 0.5px;
    line-height: 18px;
    padding: 0 26px 0 22px;
    clip-path: polygon(0 0, 100% 0, 91% 100%, 0 100%);
  }
  .services-list { list-style: none; margin-top: 4px; }
  .services-list li {
    display: flex;
    align-items: center;
    gap: 8px;
    font-size: 14.5px;
    letter-spacing: 0.3px;
    height: 22.4px;
  }
  .services-list svg { width: 14px; height: 14px; flex: none; }

  .person {
    position: absolute;
    left: 29px;
    top: 190px;
  }
  .person-name {
    font-family: "Marcellus", Georgia, serif;
    font-size: 25px;
    letter-spacing: 1px;
    line-height: 1;
  }
  .person-role { font-size: 13.5px; margin-top: 10px; color: var(--ink-soft); }
  .contact-list { list-style: none; margin-top: 16px; }
  .contact-list li {
    display: flex;
    align-items: center;
    gap: 6px;
    font-size: 13.5px;
    height: 25px;
    letter-spacing: 0.4px;
  }
  .contact-list .phone { letter-spacing: 2px; font-size: 14px; }
  .contact-list svg { width: 15px; height: 15px; flex: none; }
</style>
</head>
<body>

<section class="card card--services" aria-label="Card back: services">
  <div class="brand brand--centered">
    <div class="brand-name">HARBORLINE BUILDERS</div>
  </div>

  <div class="services">
    <p class="services-heading">Our services are<br>100% guaranteed</p>
    <span class="services-band">SPECIALIZING IN:</span>
    <ul class="services-list">
      <li><svg viewBox="0 0 14 14"><rect x="1" y="2" width="11" height="11" fill="none" stroke="currentColor" stroke-width="1.6"/><path d="M3.5 7l3 3L13 2" fill="none" stroke="currentColor" stroke-width="2"/></svg>Remodel: Kitchen &amp; Bath</li>
      <li><svg viewBox="0 0 14 14"><rect x="1" y="2" width="11" height="11" fill="none" stroke="currentColor" stroke-width="1.6"/><path d="M3.5 7l3 3L13 2" fill="none" stroke="currentColor" stroke-width="2"/></svg>Painting: Interior &amp; Exterior</li>
      <li><svg viewBox="0 0 14 14"><rect x="1" y="2" width="11" height="11" fill="none" stroke="currentColor" stroke-width="1.6"/><path d="M3.5 7l3 3L13 2" fill="none" stroke="currentColor" stroke-width="2"/></svg>Flooring: Carpet, Vinyl, Wood</li>
      <li><svg viewBox="0 0 14 14"><rect x="1" y="2" width="11" height="11" fill="none" stroke="currentColor" stroke-width="1.6"/><path d="M3.5 7l3 3L13 2" fill="none" stroke="currentColor" stroke-width="2"/></svg>Window &amp; Door Replacement</li>
      <li><svg viewBox="0 0 14 14"><rect x="1" y="2" width="11" height="11" fill="none" stroke="currentColor" stroke-width="1.6"/><path d="M3.5 7l3 3L13 2" fill="none" stroke="currentColor" stroke-width="2"/></svg>Plumbing: Repairs &amp; Upgrades</li>
      <li><svg viewBox="0 0 14 14"><rect x="1" y="2" width="11" height="11" fill="none" stroke="currentColor" stroke-width="1.6"/><path d="M3.5 7l3 3L13 2" fill="none" stroke="currentColor" stroke-width="2"/></svg>Energy-Efficient Upgrades</li>
      <li><svg viewBox="0 0 14 14"><rect x="1" y="2" width="11" height="11" fill="none" stroke="currentColor" stroke-width="1.6"/><path d="M3.5 7l3 3L13 2" fill="none" stroke="currentColor" stroke-width="2"/></svg>Deck &amp; Patio Construction</li>
      <li><svg viewBox="0 0 14 14"><rect x="1" y="2" width="11" height="11" fill="none" stroke="currentColor" stroke-width="1.6"/><path d="M3.5 7l3 3L13 2" fill="none" stroke="currentColor" stroke-width="2"/></svg>Water &amp; Mold Damage</li>
      <li><svg viewBox="0 0 14 14"><rect x="1" y="2" width="11" height="11" fill="none" stroke="currentColor" stroke-width="1.6"/><path d="M3.5 7l3 3L13 2" fill="none" stroke="currentColor" stroke-width="2"/></svg>Garage Renovation</li>
    </ul>
  </div>
</section>

<section class="card card--contact" aria-label="Card front: contact">
  <div class="brand brand--left">
    <div class="brand-name">HARBORLINE BUILDERS</div>
  </div>

  <div class="person">
    <div class="person-name">MARCUS DELLING</div>
    <div class="person-role">Business development manager</div>
    <ul class="contact-list">
      <li class="phone"><svg viewBox="0 0 16 16"><path d="M4 1l2.5 3.5-1.6 1.6c.8 1.9 2.5 3.6 4.4 4.4l1.6-1.6L14.4 11.4 13 14.5C7 14 2 9 1.5 3z" fill="currentColor"/></svg>858-471-6093</li>
      <li><svg viewBox="0 0 16 16"><rect x="1" y="3" width="14" height="10" fill="currentColor"/><path d="M1 3.5l7 5 7-5" fill="none" stroke="#1f1f20" stroke-width="1.4"/></svg>md@brightoakbuilders.com</li>
      <li><svg viewBox="0 0 16 16" fill="none" stroke="currentColor" stroke-width="1.3"><circle cx="8" cy="8" r="6.5"/><ellipse cx="8" cy="8" rx="2.8" ry="6.5"/><path d="M1.5 8h13M2.5 4.8h11M2.5 11.2h11"/></svg>www.brightoakbuilders.com</li>
    </ul>
  </div>
</section>

</body>
</html>
```